Business card por a urban DJ, up scale audience target

Need a sober design, modern, conservative colors but i can consider some options, y play rnb, hip hop, EDM and top40.

Business card for contact and personal info, double sided, use logo attrached please; im 42 so i need a card acording to my age an target audience.

Target Market(s)

Adult people, up scale audience

Industry/Entity Type

Music Download

Contact Information for Business Card

Cel (318) 4207265518 www.lumadrift.com

Requirements
Must have
• open mind
Nice to have
• open mind
Should not have
• DJ

```html
<!DOCTYPE html>
<html lang="en">
<head>
<meta charset="UTF-8">
<title>LUMA – Business Card</title>
<link href="https://fonts.googleapis.com/css2?family=Orbitron:wght@700;900&family=Exo+2:wght@500&display=swap" rel="stylesheet">
<style>
  :root {
    --backdrop: #4f5d66;
    --card: #4a4a4a;
    --ink-light: #ffffff;
    --ink-dark: #474747;
    --photo-top: #f2f2f2;
    --photo-mid: #c9c9c9;
    --photo-low: #8a8a8a;
    --photo-base: #4e4e4e;
  }
  * { margin: 0; padding: 0; box-sizing: border-box; }
  html, body { width: 1200px; height: 900px; overflow: hidden; }
  body {
    background: var(--backdrop);
    display: flex;
    flex-direction: column;
    align-items: center;
    justify-content: center;
    gap: 60px;
  }
  .card {
    position: relative;
    width: 620px;
    height: 354px;
    background: var(--card);
    overflow: hidden;
  }
  .brand {
    display: flex;
    flex-direction: column;
    align-items: center;
  }
  .brand-name {
    font-family: "Orbitron", sans-serif;
    font-weight: 900;
    font-size: 96px;
    line-height: 1;
    letter-spacing: 4px;
  }
  .brand-genres {
    margin-top: 14px;
    font-family: "Orbitron", sans-serif;
    font-weight: 700;
    font-size: 19px;
    letter-spacing: 2px;
    word-spacing: 10px;
  }
  .card-front .brand {
    position: absolute;
    inset: 0;
    justify-content: center;
    color: var(--ink-light);
  }
  .card-back .photo {
    position: absolute;
    left: 0; top: 0;
  }
  .card-back .brand {
    position: absolute;
    left: 14px;
    top: 78px;
    width: 280px;
    color: var(--ink-dark);
  }
  .card-back .brand-name { font-size: 84px; }
  .card-back .brand-genres { font-size: 16px; }
  .contact {
    position: absolute;
    left: 372px;
    top: 162px;
    list-style: none;
    color: var(--ink-light);
    font-family: "Exo 2", sans-serif;
    font-weight: 500;
    font-size: 19px;
    letter-spacing: 1px;
  }
  .contact li {
    display: flex;
    align-items: center;
    gap: 10px;
    margin-bottom: 20px;
  }
  .contact svg { flex: none; }
</style>
</head>
<body>

  <section class="card card-front">
    <div class="brand">
      <span class="brand-name">LUMA</span>
      <span class="brand-genres">RNB HIPHOP EDM</span>
    </div>
  </section>

  <section class="card card-back">
    <svg class="photo" width="620" height="354" viewBox="0 0 620 354" role="img" aria-label="Black and white photo of a concert crowd with raised hands under stage lights">
      <defs>
        <linearGradient id="crowdTone" x1="0" y1="0" x2="0" y2="1">
          <stop offset="0" stop-color="var(--photo-top)"/>
          <stop offset="0.45" stop-color="var(--photo-mid)"/>
          <stop offset="0.7" stop-color="var(--photo-low)"/>
          <stop offset="1" stop-color="var(--photo-base)"/>
        </linearGradient>
      </defs>
      <polygon points="0,0 322,0 278,354 0,354" fill="url(#crowdTone)"/>
    </svg>

    <div class="brand">
      <span class="brand-name">LUMA</span>
      <span class="brand-genres">RNB HIPHOP EDM</span>
    </div>

    <ul class="contact">
      <li>
        <svg width="14" height="22" viewBox="0 0 14 22" aria-hidden="true">
          <rect x="1" y="1" width="12" height="20" rx="2" fill="none" stroke="#fff" stroke-width="1.6"/>
          <line x1="1" y1="16" x2="13" y2="16" stroke="#fff" stroke-width="1.2"/>
          <circle cx="7" cy="18.5" r="1" fill="#fff"/>
        </svg>
        <span>(318) 4207265518</span>
      </li>
      <li>
        <svg width="20" height="20" viewBox="0 0 20 20" aria-hidden="true">
          <circle cx="10" cy="10" r="9" fill="none" stroke="#fff" stroke-width="1.6"/>
          <ellipse cx="10" cy="10" rx="4" ry="9" fill="none" stroke="#fff" stroke-width="1.2"/>
          <line x1="1" y1="10" x2="19" y2="10" stroke="#fff" stroke-width="1.2"/>
        </svg>
        <span>www.lumadrift.com</span>
      </li>
    </ul>
  </section>

</body>
</html>
```